Calder Aviation website

We are an aviation company based in Miramar, FL but with worldwide coverage. We are involved in commercial aircraft (mostly freighters) trading, sale & leasing. Specifically, we specialized in freighters of the Veltram family (V316, V328, V335, V342, V359). We also assist with financing, sale/leaseback. Handle special aviation projects and provide consultancy services. Currently engaged in a Veltram 359 passenger to Freighter conversion (P2F).

Website Preliminary Initial Content/Sections as follows:

About Us
Founded in 2011, Calder Aviation's management has many years of experience in Aviation, a strong background in scheduled airlines with emphasis in all cargo operations, freight forwarding supply chain and freight logistics, as well as ACMI and CMI operations.

Calder’s focuses in facilitating wet and dry lease operations, charter and ACMI programs consultancy, aircraft sales, leasing and procurement, aviation consultancy and aircraft management.

Calder team is a hands-on reliable alternative that works toward achieving your aircraft and aviation objectives by meeting your requirements and timeframe throughout professional and personalized service.

Tiberio Salcedo has over three decades of experience in the aviation field including aircraft maintenance, airline management, supply chain and logistics management. Tiberio is a true entrepreneur with proven experience and expertise on the multiple facets of the commercial aviation industry throughout the creation and development of a cluster of aviation entities. Tiberio is the founder and former sole member/chairman of 64 Air, a Veltram 342 All-Cargo U.S. Certificated Air Carrier created from scratch in 2014 which nowadays conforms a superb growing airline platform with an immaculate compliance operational record.

Services

Aircraft Finance, Trading, Procurement and Leasing
Calder buys, sells, leases and facilitates aircraft trading while specializes in structured aircraft investment projects. Calder has deep industry relationships and years of expertise, allowing to successfully execute lease transactions. We assist airlines, financial institutions and leasing companies when selling or purchasing aircraft.

Aircraft Available for Sale/Lease

Sale/Leaseback
Sale-leaseback is a method of financing. If your company needs liquidity, your aircraft or engine can serve as collateral for a loan throughout a sale-leaseback transaction. Sale-leaseback can free the equity tied up in aircraft or asset. Even if there is no pressing need for funds, a sale-leaseback allows you to use the equity tied up in your aircraft in a more productive fashion. Leaseback arrangements are usually employed because they confer financing, accounting or taxation benefits.

Passenger to Freighter Conversion (P2F)
Pandemic has seen the resurgence of operators packing freight into the main cabins of passenger aircraft. Carriers have been allowed to transport cargo in the cabin by removing passenger seats completely. NAB/CARO have established exemptions that allow operators to fly in “Preighter” configuration for a limited time. Calder is closely working with a U.S. group that is developing a Class E Supplemental Type Certificate (STC) for applicability on V359 aircraft which will include a cargo door for containerized freight. Final approvals are expected during first quarter of 2022.
Wet lease
Throughout our deep relationships within the industry, Calder facilitates short or long-term wet leases to airlines and qualified parties around the globe, whereby we provide the Aircraft, Crews, Maintenance and Insurance (ACMI) worldwide services at competitive rates. We also specialize in AM leases where the aircraft is registered onto Lessee´s AOC with all maintenance services included in the rates, covering all maintenance risks, or CM or CMI where the client provides the aircraft.

Dry Lease
We offer aircraft from our own portfolio on dry lease or could engage in procuring the aircraft of your choice.

Asset & Aircraft Management
We provide aircraft owners Aircraft Management services, where we manage the technical side of the aircraft or the asset. Calder also provides Harlow Dynamics engines trading, repair and full management services. We also buy Veltram/Skylane surplus inventory.

Worldwide Charters
We facilitate the arrangement of full charters to airlines and logistics companies. Certain territory restrictions may apply.

Aviation Consultancy
We provide airline consultancy services for new or special projects. Calder also specializes on All Cargo International route analysis, implementation and development. Our team provides professional guidance in obtaining worldwide both scheduled and charter authority.

Target Market(s)

Our target market are the airlines, logistics companies and commercial aviation related entities

Industry/Entity Type

Commercial Aviation

Coding

Coded - Design and coding required

Number of Pages Required

3 page

Requirements
Must have
• Illustrations of wide body freighters such V359, V342, V328

```html
<!DOCTYPE html>
<html lang="en">
<head>
<meta charset="utf-8">
<title>Calder Aviation</title>
<link rel="stylesheet" href="https://fonts.googleapis.com/css2?family=Cinzel:wght@400;500&family=Lato:wght@400;700&family=Roboto:wght@400;700&display=swap">
<style>
:root{
  --navy:#0b1338;
  --navy-deep:#070d2b;
  --steel:#b3bfc7;
  --mist:#eff1f3;
  --ink:#222630;
  --muted:#555b66;
  --white:#ffffff;
}
*{box-sizing:border-box;margin:0;padding:0}
html,body{width:1200px;height:4418px;overflow:hidden}
body{position:relative;background:var(--white);font-family:"Lato",sans-serif;color:var(--ink)}
.abs{position:absolute}

/* header */
.site-header{left:0;top:0;width:1200px;height:110px;background:var(--navy)}
.brand{left:112px;top:40px;display:flex;align-items:center;gap:10px;color:var(--white);font-family:"Lato",sans-serif;font-weight:700;font-size:22px;line-height:1;white-space:nowrap}
.brand-square{width:12px;height:12px;background:var(--white)}
.main-nav{left:392px;top:50px;display:flex;gap:17px;font-size:14px;color:var(--white)}
.call-box{left:928px;top:0;width:272px;height:110px;background:var(--steel);display:flex;align-items:center;padding-left:26px;gap:14px;color:var(--navy)}
.call-box small{display:block;font-size:14px;font-weight:700}
.call-box strong{display:block;font-size:20px;font-weight:700;letter-spacing:.3px}

/* hero */
.hero{left:0;top:110px}
.hero-panel{left:112px;top:280px;width:488px;height:270px;background:rgba(38,96,200,.72);padding:50px 0 0 42px}
.hero-title{font-family:"Cinzel",serif;font-size:56px;line-height:.95;color:var(--white)}
.hero-btn{margin-top:24px;display:inline-block;background:#b9bec4;color:#333;font-size:14px;padding:10px 20px}
.dots{left:566px;top:698px}
.down-arrow{left:579px;top:815px;width:42px;height:42px;border-radius:50%;background:var(--white);display:flex;align-items:center;justify-content:center}

/* about */
.about-block{left:60px;top:965px;width:192px;height:456px;background:var(--navy)}
.about-photo{left:112px;top:965px;width:456px;height:405px;background:linear-gradient(180deg,#7b84a6 0%,#d7a26a 55%,#3e3f48 80%,#2b2c33 100%)}
.about-copy{left:599px;top:958px;width:492px}
.eyebrow{font-family:"Cinzel",serif;font-size:18px;color:var(--ink)}
.about-copy h2{font-family:"Cinzel",serif;font-weight:400;font-size:40px;margin:4px 0 16px;color:var(--ink)}
.about-copy p{font-size:12.4px;line-height:22px;color:var(--muted);margin-bottom:21px}
.btn-dark{display:inline-block;background:var(--navy);color:var(--white);font-family:"Cinzel",serif;font-size:15px;padding:11px 20px}

/* services */
.services-band{left:0;top:1460px}
.section-title{width:1200px;left:0;text-align:center;font-family:"Cinzel",serif;font-size:36px;letter-spacing:1px}
.service-label{text-align:center;color:var(--white);font-family:"Cinzel",serif;font-size:21px;line-height:26px;width:260px}

/* offerings */
.offer-bg{left:0;top:2295px;width:1200px;height:770px;background:var(--mist)}
.divider{width:1px;background:#dfe2e6;top:2475px;height:480px}
.offer{width:300px;text-align:center}
.offer svg{display:block;margin:0 auto}
.offer h3{font-family:"Lato",sans-serif;font-weight:700;font-size:21px;line-height:26px;color:var(--ink);margin-top:10px}

/* news */
.news-card{width:310px;height:433px;background:var(--white);box-shadow:0 2px 10px rgba(0,0,0,.12);text-align:center}
.news-img{width:310px;height:218px}
.news-card h3{font-family:"Lato",sans-serif;font-weight:400;font-size:21px;line-height:25px;margin:24px 20px 10px;color:var(--ink)}
.news-date{font-size:13px;color:var(--ink);display:flex;justify-content:center;align-items:center;gap:5px}
.news-card p{font-size:12.5px;line-height:21px;color:var(--muted);margin:8px 26px 0}

/* footer */
.footer-shape{left:0;top:3800px}
.footer-body{color:var(--white)}
.footer-body h4{font-family:"Roboto",sans-serif;font-weight:700;font-size:22px}
.f-intro{font-family:"Roboto",sans-serif;font-size:14px}
.field{border:1px solid #c9ced8;height:40px;font-family:"Roboto",sans-serif;font-size:13px;padding:12px 14px;color:var(--white)}
.submit{background:var(--white);color:var(--navy);font-family:"Roboto",sans-serif;font-weight:700;font-size:17px;text-align:center;line-height:50px}
.contact-row{display:flex;gap:16px;font-family:"Roboto",sans-serif;font-size:14px;line-height:20px}
.links{list-style:none;font-family:"Roboto",sans-serif;font-size:14px;line-height:25.8px}
.links li::before{content:"»";margin-right:14px}
.bottom-bar{left:0;top:4300px;width:1200px;height:118px;background:var(--navy-deep);color:var(--white);font-family:"Roboto",sans-serif;font-size:13px}
.social{width:40px;height:40px;border-radius:50%;background:#1a2250;display:flex;align-items:center;justify-content:center;font-size:14px;font-weight:700}
</style>
</head>
<body>

<header class="abs site-header">
  <div class="abs brand"><span class="brand-square"></span><span>Calder Aviation</span></div>
  <nav class="abs main-nav"><span>HOME</span><span>ABOUT US</span><span>BLOG</span><span>SERVICES</span><span>GALLERY</span><span>CONTACT US</span></nav>
  <div class="abs call-box">
    <svg width="48" height="48" viewBox="0 0 48 48"><circle cx="24" cy="24" r="21" fill="none" stroke="#0b1338" stroke-width="3"/><path d="M15 14c2-2 4-1 5 1l2 4c1 2 0 3-1 4 1 3 4 6 7 7 1-1 2-2 4-1l4 2c2 1 3 3 1 5-4 4-10 2-16-4s-8-14-6-18z" fill="#0b1338"/></svg>
    <div><small>Call us Today :</small><strong>+1 555 014 2290</strong></div>
  </div>
</header>

<svg class="abs hero" width="1200" height="760" viewBox="0 0 1200 760">
  <defs><linearGradient id="sky" x1="0" y1="0" x2="0" y2="1"><stop offset="0" stop-color="#2a6fc4"/><stop offset=".55" stop-color="#7fa9d6"/><stop offset="1" stop-color="#dbe6ef"/></linearGradient></defs>
  <polygon points="0,0 1200,0 1200,635 600,730 0,635" fill="url(#sky)" role="img" aria-label="Photograph of a wide body jet flying above the clouds"/>
  <polygon points="0,635 600,730 1200,635 1200,668 600,750 0,668" fill="#b3bfc7"/>
</svg>
<div class="abs hero-panel">
  <div class="hero-title">CALDER<br>AVIATION</div>
  <span class="hero-btn">GET STARTED</span>
</div>
<svg class="abs dots" width="70" height="30" viewBox="0 0 70 30"><rect x="6" y="11" width="9" height="9" transform="rotate(45 10.5 15.5)" fill="#fff"/><rect x="26" y="6" width="19" height="19" transform="rotate(45 35.5 15.5)" fill="#0b1338"/><rect x="56" y="11" width="9" height="9" transform="rotate(45 60.5 15.5)" fill="#fff"/></svg>
<div class="abs down-arrow"><svg width="16" height="16" viewBox="0 0 16 16"><path d="M8 2v10M3 8l5 5 5-5" stroke="#0b1338" stroke-width="2.5" fill="none"/></svg></div>

<section>
  <div class="abs about-block"></div>
  <div class="abs about-photo" role="img" aria-label="Photograph of a jet parked on the apron at sunset"></div>
  <div class="abs about-copy">
    <div class="eyebrow">ABOUT US</div>
    <h2>CALDER AVIATION</h2>
    <p>Founded in 2011, Calder Aviation's management has many years of experience in Aviation, a strong background in scheduled airlines with emphasis in all cargo operations, freight forwarding supply chain and freight logistics, as well as ACMI and CMI operations. Calder’s focuses in facilitating wet and dry lease operations, charter and ACMI programs consultancy, aircraft sales, leasing and procurement, aviation consultancy and aircraft management.</p>
    <p>Calder team is a hands-on reliable alternative that works toward achieving your aircraft and aviation objectives by meeting your requirements and timeframe throughout professional and personalized service. Tiberio Salcedo has over three decades of experience in the aviation field including aircraft maintenance, airline management, supply chain and logistics management.</p>
    <span class="btn-dark">LEARN MORE</span>
  </div>
</section>

<svg class="abs services-band" width="1200" height="840" viewBox="0 0 1200 840">
  <defs>
    <linearGradient id="sv1" x1="0" y1="0" x2="1" y2="1"><stop offset="0" stop-color="#3ab0e6"/><stop offset="1" stop-color="#c9d3dc"/></linearGradient>
    <linearGradient id="sv2" x1="0" y1="0" x2="1" y2="1"><stop offset="0" stop-color="#1e2a3a"/><stop offset=".5" stop-color="#2f7a3a"/><stop offset="1" stop-color="#b8343a"/></linearGradient>
    <linearGradient id="sv3" x1="0" y1="0" x2="1" y2="1"><stop offset="0" stop-color="#c89a7a"/><stop offset=".5" stop-color="#3c5f96"/><stop offset="1" stop-color="#e0b030"/></linearGradient>
  </defs>
  <polygon points="0,125 600,14 1200,125" fill="#b3bfc7"/>
  <polygon points="0,134 600,40 1200,134 1200,717 600,820 0,717" fill="#0b1338"/>
  <polygon points="0,717 600,820 1200,717 1200,730 600,834 0,730" fill="#b3bfc7"/>
  <polygon points="257,288 380,430 257,572 113,430" fill="url(#sv1)" role="img" aria-label="Illustration of freighter aircraft models"/>
  <polygon points="600,222 792,430 600,638 408,430" fill="#fff"/>
  <polygon points="600,232 782,430 600,628 418,430" fill="url(#sv2)" role="img" aria-label="Photograph of a hand holding a phone with market charts"/>
  <polygon points="943,288 1088,430 943,572 808,430" fill="url(#sv3)" role="img" aria-label="Photograph of a hand signing a lease document"/>
</svg>
<div class="abs section-title" style="top:1600px;color:#fff">OUR SERVICES</div>
<div class="abs service-label" style="left:127px;top:2050px">AIRCRAFT<br>FINANCE</div>
<div class="abs service-label" style="left:470px;top:2117px">TRADING</div>
<div class="abs service-label" style="left:813px;top:2050px">PROCUREMENT<br>AND LEASING</div>

<section>
  <div class="abs offer-bg"></div>
  <div class="abs section-title" style="top:2388px;color:var(--ink)">AIRCRAFT AVAILABLE FOR SALE/LEASE</div>
  <div class="abs divider" style="left:438px"></div>
  <div class="abs divider" style="left:772px"></div>

  <div class="abs offer" style="left:125px;top:2477px">
    <svg width="154" height="154" viewBox="0 0 154 154"><rect x="32" y="32" width="90" height="90" transform="rotate(45 77 77)" fill="#dcdfe3"/><path d="M60 95h10l14-6 12-14M64 70l10-10 8 6 14-14M90 52h6v6" stroke="#0b1338" stroke-width="3" fill="none"/></svg>
    <h3>Sale/Leaseback</h3>
  </div>
  <div class="abs offer" style="left:450px;top:2477px">
    <svg width="154" height="154" viewBox="0 0 154 154"><rect x="32" y="32" width="90" height="90" transform="rotate(45 77 77)" fill="#0b1338"/><rect x="62" y="60" width="30" height="38" rx="3" stroke="#fff" stroke-width="3" fill="none"/><path d="M68 72h18M68 80h18M68 88h12" stroke="#fff" stroke-width="2.5"/></svg>
    <h3>Passenger to Freighter<br>Conversion (P2F)</h3>
  </div>
  <div class="abs offer" style="left:776px;top:2477px">
    <svg width="154" height="154" viewBox="0 0 154 154"><rect x="32" y="32" width="90" height="90" transform="rotate(45 77 77)" fill="#dcdfe3"/><path d="M77 55l16 12v30H61V67z" stroke="#0b1338" stroke-width="3" fill="none"/><rect x="68" y="74" width="7" height="7" stroke="#0b1338" stroke-width="2" fill="none"/><rect x="80" y="74" width="7" height="7" stroke="#0b1338" stroke-width="2" fill="none"/></svg>
    <h3>Dry Lease</h3>
  </div>

  <div class="abs offer" style="left:125px;top:2760px">
    <svg width="154" height="154" viewBox="0 0 154 154"><rect x="32" y="32" width="90" height="90" transform="rotate(45 77 77)" fill="#dcdfe3"/><path d="M50 80h50c6 0 8-6 2-6H80L68 62h-6l6 12H58l-4-5h-5l3 9" stroke="#0b1338" stroke-width="3" fill="none"/></svg>
    <h3>Asset &amp; Aircraft<br>Management</h3>
  </div>
  <div class="abs offer" style="left:450px;top:2760px">
    <svg width="154" height="154" viewBox="0 0 154 154"><rect x="32" y="32" width="90" height="90" transform="rotate(45 77 77)" fill="#dcdfe3"/><circle cx="77" cy="77" r="14" stroke="#0b1338" stroke-width="3" fill="none"/><path d="M63 77h28M77 63v28" stroke="#0b1338" stroke-width="2"/><path d="M56 66a24 24 0 0 1 38-10M98 88a24 24 0 0 1-38 10" stroke="#0b1338" stroke-width="3" fill="none"/></svg>
    <h3>Worldwide Charters</h3>
  </div>
  <div class="abs offer" style="left:776px;top:2760px">
    <svg width="154" height="154" viewBox="0 0 154 154"><rect x="32" y="32" width="90" height="90" transform="rotate(45 77 77)" fill="#dcdfe3"/><path d="M77 74l-8 4v10c0 6 8 10 8 10s8-4 8-10V78z" stroke="#0b1338" stroke-width="3" fill="none"/><path d="M60 62h30c4 0 4-4 0-4H78l-8-8h-4l4 8h-6l-3-3h-3l2 5" stroke="#0b1338" stroke-width="2.5" fill="none"/></svg>
    <h3>Aviation Consultancy</h3>
  </div>
</section>

<section>
  <div class="abs section-title" style="top:3160px;color:var(--ink)">LATEST NEWS</div>
  <article class="abs news-card" style="left:110px;top:3232px">
    <div class="news-img" role="img" aria-label="Photograph of a wide body jet on a taxiway" style="background:linear-gradient(180deg,#d9e3ec,#9aa6b0)"></div>
    <h3>NEMO ENIM IPSAM<br>VOLUPTATEM</h3>
    <div class="news-date"><svg width="12" height="12" viewBox="0 0 12 12"><rect x="1" y="2" width="10" height="9" fill="none" stroke="#222" stroke-width="1.5"/><path d="M1 5h10" stroke="#222"/></svg>Jan 20,2021</div>
    <p>Lorem ipsum dolor sit amet, consectetur adipiscing elit, sed do eiusmod tempor incididunt ut labore et</p>
  </article>
  <article class="abs news-card" style="left:446px;top:3232px">
    <div class="news-img" role="img" aria-label="Photograph of a passenger jet in flight" style="background:linear-gradient(180deg,#2f7fd0,#9cc6ea)"></div>
    <h3>NEMO ENIM IPSAM<br>VOLUPTATEM</h3>
    <div class="news-date"><svg width="12" height="12" viewBox="0 0 12 12"><rect x="1" y="2" width="10" height="9" fill="none" stroke="#222" stroke-width="1.5"/><path d="M1 5h10" stroke="#222"/></svg>Jan 20,2021</div>
    <p>Lorem ipsum dolor sit amet, consectetur adipiscing elit, sed do eiusmod tempor incididunt ut labore et</p>
  </article>
  <article class="abs news-card" style="left:780px;top:3232px">
    <div class="news-img" role="img" aria-label="Photograph of cargo being loaded into a freighter nose door" style="background:linear-gradient(180deg,#8a97b0,#3c3f4a)"></div>
    <h3>NEMO ENIM IPSAM<br>VOLUPTATEM</h3>
    <div class="news-date"><svg width="12" height="12" viewBox="0 0 12 12"><rect x="1" y="2" width="10" height="9" fill="none" stroke="#222" stroke-width="1.5"/><path d="M1 5h10" stroke="#222"/></svg>Jan 20,2021</div>
    <p>Lorem ipsum dolor sit amet, consectetur adipiscing elit, sed do eiusmod tempor incididunt ut labore et</p>
  </article>
  <span class="abs btn-dark" style="left:508px;top:3697px;font-size:14px;padding:12px 21px">VIEW MORE NEWS</span>
</section>

<svg class="abs footer-shape" width="1200" height="500" viewBox="0 0 1200 500">
  <polygon points="0,110 600,14 1200,110" fill="#b3bfc7"/>
  <polygon points="0,125 600,32 1200,125 1200,500 0,500" fill="#0b1338"/>
</svg>
<footer class="footer-body">
  <h4 class="abs" style="left:115px;top:3982px">GET IN TOUCH</h4>
  <p class="abs f-intro" style="left:117px;top:4034px">Lorem ipsum dolor sit amet, consectetur adipiscing elit, sed do</p>
  <div class="abs field" style="left:119px;top:4073px;width:218px">Name</div>
  <div class="abs field" style="left:355px;top:4073px;width:218px">E - Mail</div>
  <div class="abs field" style="left:119px;top:4133px;width:218px">Subject</div>
  <div class="abs field" style="left:355px;top:4133px;width:218px">Message</div>
  <div class="abs submit" style="left:120px;top:4195px;width:454px;height:50px">SUBMIT</div>

  <h4 class="abs" style="left:622px;top:3982px">CONTACT US</h4>
  <div class="abs contact-row" style="left:627px;top:4038px"><svg width="16" height="20" viewBox="0 0 16 20"><path d="M8 1a6 6 0 0 1 6 6c0 5-6 12-6 12S2 12 2 7a6 6 0 0 1 6-6z" fill="none" stroke="#fff" stroke-width="1.5"/><circle cx="8" cy="7" r="2" fill="#fff"/></svg><span>123,Lorem ipsum dolor sit amet,<br>consectetur adipiscing</span></div>
  <div class="abs contact-row" style="left:627px;top:4100px"><svg width="18" height="18" viewBox="0 0 18 18"><path d="M3 2c1-1 2 0 3 1l1 2c0 1 0 2-1 2 1 2 3 4 5 5 0-1 1-1 2-1l2 1c1 1 2 2 1 3-2 2-5 1-9-3S1 4 3 2z" fill="none" stroke="#fff" stroke-width="1.3"/></svg><span>Phone: +1 555 014 2290</span></div>
  <div class="abs contact-row" style="left:627px;top:4166px"><svg width="18" height="18" viewBox="0 0 18 18"><rect x="2" y="6" width="14" height="9" fill="none" stroke="#fff" stroke-width="1.5"/><rect x="5" y="2" width="8" height="5" fill="none" stroke="#fff" stroke-width="1.5"/></svg><span>Fax: +65 5550 1180</span></div>
  <div class="abs contact-row" style="left:627px;top:4229px"><svg width="18" height="18" viewBox="0 0 18 18"><rect x="1" y="4" width="16" height="11" fill="none" stroke="#fff" stroke-width="1.3"/><path d="M1 4l8 6 8-6" fill="none" stroke="#fff" stroke-width="1.3"/></svg><span>Email: info@calderaviation.example</span></div>

  <h4 class="abs" style="left:955px;top:3982px">QUICK LINKS</h4>
  <ul class="abs links" style="left:955px;top:4028px">
    <li>Home</li><li>About us</li><li>Services</li><li>Team</li><li>Why us?</li><li>Price</li><li>Client</li><li>Career</li><li>Contact</li>
  </ul>
</footer>

<div class="abs bottom-bar">
  <div class="abs" style="left:109px;top:50px">Login | Register | Privacy policy | Terms &amp; conditions</div>
  <div class="abs social" style="left:554px;top:39px">f</div>
  <div class="abs social" style="left:606px;top:39px">t</div>
  <div class="abs" style="left:775px;top:50px">(c) 2021 Calder Aviation | All Rights Reserved</div>
</div>

</body>
</html>
```